Automotive Accessories Business Card

Design a business template that match our new logo design and our industry.

https://www.qelmotorgear.com/

Target Market(s)

Aftermarket auto parts and accessories

Industry/Entity Type

automotive

Contact Information for Business Card

company logo

Font styles to use
Serif
Sans Serif

Colors
EB3D1F
EC4F4E
F09395
F8D3D4
FCEDEE

```html
<!DOCTYPE html>
<html lang="en">
<head>
<meta charset="utf-8">
<title>QEL Motor Gear – Business Card</title>
<link rel="stylesheet" href="https://fonts.googleapis.com/css2?family=Montserrat:wght@800&family=Open+Sans:wght@400;700&display=swap">
<style>
  :root {
    --page-bg: #e9e6e3;
    --card-white: #f4f4f4;
    --band-dark: #2f2f30;
    --band-dark-light: #434345;
    --brand-red: #d9262e;
    --ink-dark: #2b2b2d;
    --text-light: #f2f2f2;
    --text-muted: #d6d6d6;
    --back-dark: #1f1f20;
    --back-mid: #6a6a6c;
  }
  * { box-sizing: border-box; margin: 0; padding: 0; }
  html, body { width: 1200px; height: 960px; overflow: hidden; }
  body {
    background: var(--page-bg);
    font-family: "Open Sans", Arial, sans-serif;
    display: flex;
    flex-direction: column;
    align-items: center;
    justify-content: center;
    gap: 56px;
  }
  .card {
    width: 720px;
    height: 412px;
    border-radius: 4px;
    overflow: hidden;
    box-shadow: 0 10px 28px rgba(0,0,0,0.22);
    position: relative;
  }
  .card-front { background: var(--card-white); }
  .front-top { position: absolute; inset: 0 0 auto 0; height: 196px; }
  .brand {
    position: absolute;
    right: 52px;
    top: 78px;
    display: flex;
    align-items: center;
    gap: 14px;
  }
  .brand-square { width: 30px; height: 30px; background: var(--brand-red); }
  .brand-name {
    font-family: "Montserrat", Arial, sans-serif;
    font-weight: 800;
    font-size: 30px;
    letter-spacing: 1px;
    color: var(--ink-dark);
    text-transform: uppercase;
  }
  .front-band {
    position: absolute;
    left: 0; right: 0; bottom: 0;
    height: 216px;
    background: linear-gradient(135deg, var(--band-dark-light), var(--band-dark) 70%);
  }
  .person {
    position: absolute;
    left: 52px;
    top: 52px;
    width: 220px;
    text-align: right;
  }
  .person-name {
    font-family: "Montserrat", Arial, sans-serif;
    font-weight: 800;
    font-size: 28px;
    color: var(--text-light);
    letter-spacing: 1px;
    line-height: 1.15;
  }
  .person-title { font-size: 16px; color: var(--text-muted); margin-top: 4px; }
  .divider {
    position: absolute;
    left: 300px;
    top: 40px;
    width: 3px;
    height: 120px;
    background: var(--brand-red);
  }
  .contacts {
    position: absolute;
    left: 330px;
    top: 46px;
    list-style: none;
  }
  .contact {
    display: flex;
    align-items: center;
    gap: 12px;
    font-size: 18px;
    color: var(--text-light);
    height: 36px;
  }
  .contact svg { width: 18px; height: 18px; fill: none; stroke: var(--text-light); stroke-width: 1.6; flex: none; }
  .contact .web-strong { font-weight: 700; }
  .card-back {
    background: radial-gradient(ellipse at 25% 15%, var(--back-mid), var(--back-dark) 75%);
  }
</style>
</head>
<body>
  <section class="card card-front">
    <div class="front-top">
      <div class="brand">
        <span class="brand-square"></span>
        <span class="brand-name">QEL Motor Gear Inc</span>
      </div>
    </div>
    <div class="front-band">
      <div class="person">
        <p class="person-name">DANA REYES</p>
        <p class="person-title">Sales Manager</p>
      </div>
      <span class="divider"></span>
      <ul class="contacts">
        <li class="contact">
          <svg viewBox="0 0 24 24"><path d="M6 3l3 1 1 5-2 1c1 3 3 5 6 6l1-2 5 1 1 3-2 3C11 21 3 13 3 5z"/></svg>
          1-800-555-0142
        </li>
        <li class="contact">
          <svg viewBox="0 0 24 24"><rect x="3" y="6" width="18" height="12"/><path d="M3 6l9 7 9-7"/></svg>
          sales@qelmotorgear.com
        </li>
        <li class="contact">
          <svg viewBox="0 0 24 24"><circle cx="12" cy="12" r="9"/><path d="M3 12h18M12 3c3 3 3 15 0 18M12 3c-3 3-3 15 0 18"/></svg>
          <span>www.<span class="web-strong">qelmotorgear</span>.com</span>
        </li>
      </ul>
    </div>
  </section>
  <section class="card card-back" role="img" aria-label="Dark checkered racing flag pattern"></section>
</body>
</html>
```